Meridale Bed Company Needs Business Card

Looking for a very nice looking business card. Creative but not extravagant. We sell beds and pillows across the U.S. and need something professional but catchy. I have attached the logo.

Name : Devin Holt
Title : President
Phone : (800) 471-2960
Email: sleep@quilmora.com
Website: www.quilmora.com

Can be single-sided or double-sided
horizontal or vertical

Can use Blues/Greys

Target Market(s)

Mass Market

Industry/Entity Type

Retail

Contact Information for Business Card

Name : Devin Holt
Title : President
Phone : (800) 471-2960
Email: sleep@quilmora.com
Website: www.quilmora.com

Requirements
Must have
• Clean, Modern, Smooth
• Can use Blues/Greys
• On the other side without the information - have something simple like www.quilmora.com or our logo
Nice to have
• Surprise me
Should not have
• Nothing crazy, nothing cluttered

```html
<!DOCTYPE html>
<html lang="en">
<head>
<meta charset="utf-8">
<title>Quilmora Business Card</title>
<link rel="stylesheet" href="https://fonts.googleapis.com/css2?family=Montserrat:wght@400;700&display=swap">
<style>
  :root {
    --backdrop: #2a2a2a;
    --card: #030303;
    --brand-blue: #2fa6dc;
    --rule-grey: #8a8a8a;
    --text-white: #f2f2f2;
  }
  * { margin: 0; padding: 0; box-sizing: border-box; }
  html, body { width: 1200px; height: 900px; overflow: hidden; }
  body {
    background: var(--backdrop);
    display: flex;
    flex-direction: column;
    align-items: center;
    justify-content: center;
    gap: 56px;
    font-family: "Montserrat", sans-serif;
  }
  .card {
    position: relative;
    width: 630px;
    height: 360px;
    background: var(--card);
    border-radius: 22px;
    overflow: hidden;
    box-shadow: 0 14px 30px rgba(0,0,0,0.45);
  }
  .accent-band {
    position: absolute;
    top: 0; bottom: 0;
    width: 40px;
    background: var(--brand-blue);
  }
  .accent-band::before,
  .accent-band::after {
    content: "";
    position: absolute;
    top: 0; bottom: 0;
    width: 1.5px;
    background: var(--rule-grey);
  }
  .accent-band::before { left: -6px; }
  .accent-band::after { right: -6px; }
  .brand-name {
    font-family: "Montserrat", sans-serif;
    font-weight: 400;
    color: var(--brand-blue);
    line-height: 1;
    white-space: nowrap;
  }

  /* Front */
  .card-front .accent-band { left: 548px; }
  .card-front .brand-name {
    position: absolute;
    left: 0; width: 540px;
    top: 128px;
    text-align: center;
    font-size: 80px;
  }
  .card-front .site {
    position: absolute;
    left: 0; width: 540px;
    bottom: 34px;
    text-align: center;
    color: var(--text-white);
    font-size: 19px;
    letter-spacing: 0.5px;
  }
  .card-front .site .highlight { color: var(--brand-blue); }

  /* Back */
  .card-back .accent-band { left: 42px; }
  .card-back .brand-name {
    position: absolute;
    left: 128px;
    top: 58px;
    font-size: 72px;
  }
  .contact-block {
    position: absolute;
    left: 128px;
    top: 200px;
    color: var(--text-white);
  }
  .person-name {
    color: var(--brand-blue);
    font-weight: 700;
    font-size: 27px;
    letter-spacing: 0.3px;
  }
  .person-title {
    font-size: 17px;
    margin-bottom: 12px;
  }
  .contact-list { list-style: none; }
  .contact-list li {
    display: flex;
    align-items: center;
    gap: 10px;
    font-size: 17px;
    line-height: 25px;
  }
  .contact-list svg { width: 13px; height: 13px; flex: none; }
</style>
</head>
<body>
  <section class="card card-front">
    <div class="brand-name">quilmora</div>
    <p class="site">www.<span class="highlight">quilmora</span>.com</p>
    <div class="accent-band"></div>
  </section>

  <section class="card card-back">
    <div class="accent-band"></div>
    <div class="brand-name">quilmora</div>
    <div class="contact-block">
      <p class="person-name">Devin Holt</p>
      <p class="person-title">President</p>
      <ul class="contact-list">
        <li>
          <svg viewBox="0 0 24 24" aria-hidden="true"><path fill="#2fa6dc" d="M6.6 10.8a15.1 15.1 0 0 0 6.6 6.6l2.2-2.2a1 1 0 0 1 1-.25 11.4 11.4 0 0 0 3.6.57 1 1 0 0 1 1 1V20a1 1 0 0 1-1 1A17 17 0 0 1 3 4a1 1 0 0 1 1-1h3.5a1 1 0 0 1 1 1c0 1.25.2 2.45.57 3.57a1 1 0 0 1-.25 1z"/></svg>
          (800) 471-2960
        </li>
        <li>
          <svg viewBox="0 0 24 24" aria-hidden="true"><rect x="2" y="5" width="20" height="14" rx="2" fill="none" stroke="#2fa6dc" stroke-width="2.4"/><path d="M3 6l9 7 9-7" fill="none" stroke="#2fa6dc" stroke-width="2.4"/></svg>
          sleep@quilmora.com
        </li>
        <li>
          <svg viewBox="0 0 24 24" aria-hidden="true"><circle cx="12" cy="12" r="9.5" fill="none" stroke="#2fa6dc" stroke-width="2.2"/><ellipse cx="12" cy="12" rx="4" ry="9.5" fill="none" stroke="#2fa6dc" stroke-width="2"/><path d="M2.5 12h19" stroke="#2fa6dc" stroke-width="2"/></svg>
          www.quilmora.com
        </li>
      </ul>
    </div>
  </section>
</body>
</html>
```